Cyber Security Site Design (Products & Consulting)

I need my website redesigned to be engaging, clean, efficient and modern. My company (when its up and running) is going to be concentrated on two things: a few specific products for cyber security as well as cyber security consulting services. The background I bring to the field is having worked with small companies all the way to the largest government organizations and advising them on their security posture and how to improve it. We need the ability to add products and services easily.

For a sample product, you can use either Tarnet (http://www.tarnet-relay.org/) or Verodyne Ashmantle (https://www.verodyne.com/products/relay-hx-and-fortified-edge-portal).

It will replace https://lumerafieldworks.com/

Target Market(s)

Cyber Security professionals in all verticals

Coding

Coded - Design and coding required

Number of Pages Required

4 page

Font styles to use
Sans Serif

Colors
6b449b

Requirements
Must have
• Ability to easily modify
• Have main page
• Have product specific pages
• Have consulting services pages
• Have executive team information
• Clean, modern design
• Usage of the logo and its color scheme
Nice to have
• I like the idea of a left collapsed sidebar (so icons only) that can expand for text.
• I am also open to a very unique landing page, possibly a shape in the middle (hexagons maybe?) with each of the options there.
Should not have
• Nothing that looks like it came out of a hacker movie

```html
<!DOCTYPE html>
<html lang="en">
<head>
<meta charset="utf-8">
<title>Lumera Fieldworks – Our Products</title>
<link href="https://fonts.googleapis.com/css2?family=Exo+2:wght@400;500;600;700&family=Roboto:wght@400;500&display=swap" rel="stylesheet">
<style>
:root{
  --brand:#6b449b;
  --brand-deep:#5a3688;
  --brand-bar:#4e2f78;
  --ink:#222;
  --text:#444;
  --icon:#4a4a4a;
  --rule:#e4e4e4;
  --white:#fff;
}
*{margin:0;padding:0;box-sizing:border-box}
html,body{width:681px;height:1200px;overflow:hidden;background:var(--white)}
body{position:relative;font-family:"Roboto",sans-serif;color:var(--text)}
.abs{position:absolute}

/* header */
.site-header{position:absolute;left:0;top:0;width:681px;height:40px;background:var(--white)}
.brand{position:absolute;left:80px;top:11px;display:flex;align-items:center;gap:5px}
.brand-mark{width:14px;height:14px;background:var(--brand);border-radius:2px}
.brand-name{font-family:"Exo 2",sans-serif;font-weight:600;font-size:15px;color:#4a4a4a;letter-spacing:.3px}
.main-nav{position:absolute;top:15px;left:258px;display:flex;gap:0;font-size:7.4px;color:#222}
.main-nav span{position:absolute;white-space:nowrap}
.main-nav .active{color:var(--brand)}
.btn{display:flex;align-items:center;gap:5px;background:var(--brand);color:var(--white);border-radius:10px;font-size:7px;font-weight:500;padding:0 8px 0 6px;height:18px;box-shadow:0 2px 4px rgba(107,68,155,.35)}
.btn-dot{width:10px;height:10px;border-radius:50%;border:1.5px solid var(--white)}

/* hero */
.hero{position:absolute;left:0;top:40px;width:681px;height:213px}
.hero-shape{position:absolute;inset:0}
.hero-title{position:absolute;top:66px;width:681px;text-align:center;font-family:"Exo 2",sans-serif;font-weight:700;font-size:25px;color:var(--white);letter-spacing:.2px}
.hero-sub{position:absolute;top:98px;width:681px;text-align:center;font-family:"Exo 2",sans-serif;font-size:10px;color:var(--white)}
.hero .btn{position:absolute;left:291px;top:127px;height:19px}

.breadcrumb{position:absolute;left:80px;top:245px;font-size:7.4px;color:#222}
.breadcrumb .sep{margin:0 6px}
.breadcrumb .here{color:var(--brand)}

/* products */
.section-title{position:absolute;top:290px;width:681px;text-align:center;font-family:"Exo 2",sans-serif;font-size:23px;color:var(--ink)}
.section-title b{font-weight:700}
.title-rule{position:absolute;left:265px;top:328px;width:152px;height:1px;background:var(--rule)}
.title-accent{position:absolute;left:329px;top:327px;width:24px;height:2px;background:var(--brand)}

.grid-line{position:absolute;background:var(--rule)}
.product{position:absolute;width:185px;text-align:center}
.product-icon{width:56px;height:56px;margin:0 auto;border-radius:50%;background:var(--icon);box-shadow:0 0 0 2px #eee;display:flex;align-items:center;justify-content:center}
.product-icon.is-active{background:var(--brand)}
.product h3{margin-top:9px;font-family:"Exo 2",sans-serif;font-weight:500;font-size:11.5px;color:#222}
.product h3.is-active{color:var(--brand)}
.product p{margin-top:5px;font-size:7.4px;line-height:11.7px;color:#444}

.feature-brand{position:absolute;left:472px;top:700px;width:120px;display:flex;flex-direction:column;align-items:center;gap:8px}
.feature-square{width:40px;height:40px;background:var(--brand)}
.feature-name{font-family:"Exo 2",sans-serif;font-weight:600;font-size:15px;color:#4a4a4a}

/* footer */
.footer-shape{position:absolute;left:0;top:845px;width:681px;height:337px}
.footer-brand{position:absolute;top:872px;width:681px;display:flex;justify-content:center;align-items:center;gap:6px}
.footer-brand .brand-mark{background:var(--white)}
.footer-brand .brand-name{color:var(--white);font-size:16px}
.footer-rule{position:absolute;left:0;top:906px;width:681px;height:1px;background:rgba(255,255,255,.1)}
.cta-title{position:absolute;left:77px;top:930px;font-family:"Exo 2",sans-serif;font-size:20px;color:var(--white)}
.cta-title b{font-weight:700}
.cta-text{position:absolute;left:80px;top:960px;width:210px;font-size:7.8px;line-height:9.5px;color:var(--white)}
.col-head{position:absolute;font-family:"Exo 2",sans-serif;font-weight:500;font-size:9px;color:var(--white)}
.col-head::after{content:"";position:absolute;left:0;top:15px;width:25px;height:1px;background:rgba(255,255,255,.6)}
.contact-row{position:absolute;left:78px;display:flex;gap:7px;color:var(--white);font-size:6px;line-height:9.5px}
.contact-row svg{flex:none;margin-top:1px}
.contact-row .org{font-weight:500;font-size:7px}
.contact-row .phone{font-weight:500;font-size:9px}
.quick-links{position:absolute;left:227px;top:1034px;list-style:none;font-size:6.2px;color:var(--white)}
.quick-links li{height:11px}
.quick-links li::before{content:"›";margin-right:6px}

.form-card{position:absolute;left:349px;top:934px;width:252px;height:217px;background:var(--white)}
.field{position:absolute;left:20px;width:212px;height:21px;border:1px solid #d6d6d6;font-size:6.8px;color:#666;padding:6px 8px}
.form-card .btn{position:absolute;left:20px;top:182px;height:18px}

.bottom-bar{position:absolute;left:0;top:1151px;width:681px;height:29px;background:var(--brand-bar)}
.copyright{position:absolute;left:80px;top:11px;font-size:6.8px;color:var(--white)}
.copyright b{font-weight:500}
.social{position:absolute;left:443px;top:6px;display:flex;gap:4px}
.social span{width:16px;height:16px;border:1px solid rgba(255,255,255,.8);border-radius:50%}
</style>
</head>
<body>

<header class="site-header">
  <div class="brand"><span class="brand-mark"></span><span class="brand-name">Lumera Fieldworks</span></div>
  <nav class="main-nav">
    <span style="left:0">HOME</span>
    <span style="left:40px">ABOUT</span>
    <span style="left:84px">OUR TEAM</span>
    <span class="active" style="left:139px">OUR PRODUCTS</span>
    <span style="left:212px">SERVICES</span>
  </nav>
  <div class="btn abs" style="left:526px;top:11px"><span class="btn-dot"></span>CONTACT US</div>
</header>

<section class="hero">
  <svg class="hero-shape" width="681" height="213" role="img" aria-label="City skyline photograph at dusk">
    <defs>
      <linearGradient id="sky" x1="0" y1="0" x2="0" y2="1">
        <stop offset="0" stop-color="#6d7e96"/>
        <stop offset=".45" stop-color="#8a7a7e"/>
        <stop offset=".75" stop-color="#7b5a48"/>
        <stop offset="1" stop-color="#4c3e38"/>
      </linearGradient>
    </defs>
    <polygon points="0,0 681,0 681,145 340,212 0,145" fill="url(#sky)"/>
  </svg>
  <h1 class="hero-title">CYBER SECURITY CONSULTING &amp; PRODUCTS</h1>
  <p class="hero-sub">A full range of Cyber Security Consulting Services and Products to meet your business requirements</p>
  <div class="btn"><span class="btn-dot"></span>GET STARTED NOW!</div>
</section>

<div class="breadcrumb">HOME<span class="sep">»</span><span class="here">OUR PRODUCTS</span></div>

<h2 class="section-title">OUR <b>PRODUCTS</b></h2>
<div class="title-rule"></div><div class="title-accent"></div>

<div class="grid-line" style="left:248px;top:347px;width:1px;height:453px"></div>
<div class="grid-line" style="left:433px;top:347px;width:1px;height:453px"></div>
<div class="grid-line" style="left:59px;top:498px;width:562px;height:1px"></div>
<div class="grid-line" style="left:59px;top:646px;width:562px;height:1px"></div>

<div class="product" style="left:64px;top:371px">
  <div class="product-icon is-active"><svg width="26" height="26" viewBox="0 0 26 26" fill="none" stroke="#fff" stroke-width="1.5"><path d="M13 2l9 3v7c0 6-4 10-9 12-5-2-9-6-9-12V5z"/><path d="M9 13l3 3 5-6"/></svg></div>
  <h3 class="is-active">Integrated Cyber Defense</h3>
  <p>Sed do eiusmod tempor incididunt ut<br>labore et dolore magna aliqua.</p>
</div>
<div class="product" style="left:248px;top:371px">
  <div class="product-icon"><svg width="28" height="28" viewBox="0 0 28 28" fill="none" stroke="#fff" stroke-width="1.5"><circle cx="12" cy="12" r="9"/><path d="M18.5 18.5l7 7"/><ellipse cx="12" cy="12" rx="6" ry="3.5"/><circle cx="12" cy="12" r="1.5"/></svg></div>
  <h3>Advance Threat Protection</h3>
  <p>Sed do eiusmod tempor incididunt ut<br>labore et dolore magna aliqua.</p>
</div>
<div class="product" style="left:433px;top:371px">
  <div class="product-icon"><svg width="28" height="28" viewBox="0 0 28 28" fill="none" stroke="#fff" stroke-width="1.4"><circle cx="16" cy="11" r="8"/><path d="M12 14v-3M15 14V8M18 14v-5"/><rect x="3" y="17" width="8" height="8"/><path d="M5 17v-3a2 2 0 014 0v3"/></svg></div>
  <h3>Information Protection</h3>
  <p>Sed do eiusmod tempor incididunt ut<br>labore et dolore magna aliqua.</p>
</div>

<div class="product" style="left:64px;top:519px">
  <div class="product-icon"><svg width="26" height="26" viewBox="0 0 26 26" fill="none" stroke="#fff" stroke-width="1.4"><path d="M5 2h10l5 5v8M5 2v22h9"/><path d="M8 9h9M8 12h9M8 15h6M8 18h5"/><rect x="15" y="17" width="9" height="7" fill="#fff"/><path d="M17 17v-2a2.5 2.5 0 015 0v2"/></svg></div>
  <h3>Endpoint Security</h3>
  <p>Sed do eiusmod tempor incididunt ut<br>labore et dolore magna aliqua.</p>
</div>
<div class="product" style="left:248px;top:519px">
  <div class="product-icon"><svg width="26" height="26" viewBox="0 0 26 26" fill="none" stroke="#fff" stroke-width="1.5"><path d="M13 2l9 3v7c0 6-4 10-9 12-5-2-9-6-9-12V5z"/><rect x="8" y="8" width="10" height="7"/><path d="M8 8l5 4 5-4M10 19l3 2 3-3"/></svg></div>
  <h3>Email Security</h3>
  <p>Sed do eiusmod tempor incididunt ut<br>labore et dolore magna aliqua.</p>
</div>
<div class="product" style="left:433px;top:519px">
  <div class="product-icon"><svg width="28" height="28" viewBox="0 0 28 28" fill="none" stroke="#fff" stroke-width="1.4"><circle cx="14" cy="14" r="12"/><ellipse cx="14" cy="14" rx="5" ry="12"/><path d="M2 14h24M4 8h20M4 20h20"/><rect x="5" y="13" width="7" height="6" fill="#fff"/></svg></div>
  <h3>Network Security</h3>
  <p>Sed do eiusmod tempor incididunt ut<br>labore et dolore magna aliqua.</p>
</div>

<div class="product" style="left:64px;top:666px">
  <div class="product-icon"><svg width="30" height="26" viewBox="0 0 30 26" fill="none" stroke="#fff" stroke-width="1.5"><path d="M8 20H6a5 5 0 010-10 8 8 0 0115-1 5.5 5.5 0 012 11h-1"/><rect x="10" y="14" width="10" height="9" fill="#fff"/><path d="M12 14v-3a3 3 0 016 0v3"/></svg></div>
  <h3>Cloud Security</h3>
  <p>Sed do eiusmod tempor incididunt ut<br>labore et dolore magna aliqua.</p>
</div>
<div class="product" style="left:248px;top:666px">
  <div class="product-icon"><svg width="28" height="28" viewBox="0 0 28 28" fill="none" stroke="#fff" stroke-width="1.3"><path d="M14 2l5 2.5v5L14 12l-5-2.5v-5z"/><path d="M7 13l5 2.5v5L7 23l-5-2.5v-5z"/><path d="M21 12l5 2.5v5L21 22l-5-2.5v-5z"/></svg></div>
  <h3>Small Business Products</h3>
  <p>Sed do eiusmod tempor incididunt ut<br>labore et dolore magna aliqua.</p>
</div>

<div class="feature-brand">
  <span class="feature-square"></span>
  <span class="feature-name">Lumera Fieldworks</span>
</div>

<svg class="footer-shape" width="681" height="337" viewBox="0 0 681 337" aria-hidden="true">
  <polygon points="0,23 340,0 681,23 681,337 0,337" fill="#673a98"/>
</svg>
<div class="footer-brand"><span class="brand-mark"></span><span class="brand-name">Lumera Fieldworks</span></div>
<div class="footer-rule"></div>

<h2 class="cta-title"><b>LET’S</b> GET STARTED</h2>
<svg class="abs" style="left:258px;top:940px" width="92" height="82" viewBox="0 0 92 82" fill="none" stroke="#fff" stroke-width=".8" stroke-dasharray="2 2" aria-hidden="true"><path d="M0 7c30-6 50 0 40 18-8 14 6 16 12 4 6-14 36-6 40 50"/></svg>
<p class="cta-text">Take the first step to growing your business with a FREE consultation and quote.</p>

<div class="col-head" style="left:78px;top:1008px">Contact Details</div>
<div class="contact-row" style="top:1033px">
  <svg width="6" height="8" viewBox="0 0 6 8"><path d="M3 0a3 3 0 00-3 3c0 2 3 5 3 5s3-3 3-5a3 3 0 00-3-3z" fill="#fff"/><circle cx="3" cy="3" r="1" fill="#673a98"/></svg>
  <div><div class="org">LUMERA FIELDWORKS</div>48 Carrow Lane, Suite<br>#210 Brennick, TX 70014.</div>
</div>
<div class="contact-row" style="top:1068px;align-items:center">
  <svg width="7" height="7" viewBox="0 0 7 7"><path d="M1 0l1.5 1.8-1 1a4 4 0 002.7 2.7l1-1L7 6 6 7C3 7 0 4 0 1z" fill="#fff"/></svg>
  <span class="phone">555-014-2290</span>
</div>
<div class="contact-row" style="top:1088px;align-items:center">
  <svg width="7" height="5" viewBox="0 0 7 5"><rect width="7" height="5" fill="#fff"/><path d="M0 0l3.5 2.5L7 0" stroke="#673a98" stroke-width=".7" fill="none"/></svg>
  <span>info@lumerafieldworks.com</span>
</div>

<div class="col-head" style="left:227px;top:1007px">Quick Links</div>
<ul class="quick-links">
  <li>Home</li><li>About Us</li><li>Our Team</li><li>Our Products</li><li>Services</li><li>Conatact</li>
</ul>

<form class="form-card">
  <div class="field" style="top:22px">First Name</div>
  <div class="field" style="top:50px">Last Name</div>
  <div class="field" style="top:78px">Email</div>
  <div class="field" style="top:106px">Phone Number</div>
  <div class="field" style="top:134px;height:34px">Message</div>
  <div class="btn"><span class="btn-dot"></span>SUBMIT</div>
</form>

<footer class="bottom-bar">
  <p class="copyright">Copyright © 2018 <b>LumeraFieldworks</b>. All Right Reserved.</p>
  <div class="social"><span></span><span></span><span></span><span></span></div>
</footer>

</body>
</html>
```